Creative, fresh business card design for Ripplecraft Facades

We need a fresh, creative business card design for Ripplecraft Facades. We are the manufacturer of Ripplecraft Facades in Australia. Wall panels are 2400 x 1200mm panels made from MDF and feature 3D patterns on the face of the panel. The colours to be used are green, silver/grey and white RGB
Red 187
Green 207
Blue 65.

An idea is to possibly use a watermark of one of our designs as a background (like on the "Grids" design on the left hand side of page 2 of our brochure).

Target Market(s)

Interior designers, architects, builders and home renovators

Industry/Entity Type

Business

Contact Information for Business Card

Details to go on the card are:
Our logo (attached),
Slogan: "Decorative panels for interiors and exteriors",
Contact name,
Position,
Mobile phone number,
Business address,
Business phone,
Business fax,
Website and
Email address.

I have attached a few images of our panels and our brochure for reference.

The colours of the business card should feature our logo colours which are: RGB
Red 187
Green 207
Blue 65

Requirements
Must have
• Very modern fonts and design. Some of the designs shown especially the "Prisms" design which is a popular design.
Nice to have
• Creative but simple design. Very contemporary.
Should not have
• Anything ornate or old fashioned.

```html
<!DOCTYPE html>
<html lang="en">
<head>
<meta charset="utf-8">
<title>Ripplecraft Facades – Business Cards</title>
<link rel="stylesheet" href="https://fonts.googleapis.com/css2?family=Arimo:wght@400;700&display=swap">
<style>
  :root {
    --brand-green: rgb(187, 207, 65);
    --panel-grey: #8c8d90;
    --text-grey: #7d7e81;
    --card-white: #ffffff;
    --backdrop: #2b2b2d;
  }
  * { box-sizing: border-box; margin: 0; padding: 0; }
  html, body { width: 1200px; height: 900px; overflow: hidden; }
  body {
    position: relative;
    background: var(--backdrop);
    font-family: "Arimo", Arial, sans-serif;
    color: var(--card-white);
  }
  .card {
    position: absolute;
    width: 514px;
    height: 297px;
    background: var(--card-white);
  }
  .card--front-dark  { left: 72px;  top: 138px; }
  .card--back-upper  { left: 616px; top: 138px; }
  .card--front-light { left: 72px;  top: 464px; }
  .card--back-lower  { left: 616px; top: 464px; }

  .block { position: absolute; }

  .panel-photo--wide { left: 21px; top: 20px; width: 471px; height: 256px; }
  .panel-photo--dark {
    background: linear-gradient(90deg, #3d3d3f 0%, #6a6a6c 40%, #9a9a9c 70%, #c9c9c9 86%, #d9cdb8 88%, #a8b4ba 94%, #e6e2dc 100%);
  }
  .panel-photo--light {
    background: linear-gradient(160deg, #f4f4f4 0%, #d9d9d9 45%, #eeeeee 70%, #cfcfcf 100%);
  }
  .panel-photo--strip {
    left: 193px; width: 299px;
    background: linear-gradient(90deg, #454547 0%, #76767a 45%, #a3a3a5 78%, #cfc6b5 86%, #8a9ca6 93%, #e3ded6 100%);
  }

  .brand-block {
    display: flex;
    align-items: center;
    justify-content: center;
    background: var(--brand-green);
    color: var(--card-white);
    font-weight: 700;
    text-align: center;
    line-height: 1.05;
  }
  .brand-block--front { left: 157px; top: 89px; width: 200px; height: 110px; font-size: 28px; }
  .brand-block--back  { left: 21px; top: 178px; width: 167px; height: 97px; font-size: 23px; }

  .tagline {
    position: absolute;
    left: 45px;
    width: 428px;
    font-size: 15px;
    letter-spacing: 3.1px;
    color: var(--text-grey);
    white-space: nowrap;
  }
  .card--back-upper .tagline { top: 17px; }
  .card--back-lower .tagline { top: 160px; }

  .person-box {
    left: 21px; width: 167px;
    background: var(--panel-grey);
    padding: 37px 0 0 20px;
    font-size: 13px;
    line-height: 17px;
  }
  .card--back-upper .person-box, .card--back-upper .panel-photo--strip { top: 45px; height: 126px; }
  .card--back-lower .person-box, .card--back-lower .panel-photo--strip { top: 20px; height: 131px; }
  .card--back-lower .person-box { padding-top: 36px; }
  .person-name { font-weight: 700; }
  .person-mobile { margin-top: 18px; }

  .contact-box {
    left: 193px; top: 178px; width: 299px; height: 97px;
    background: var(--brand-green);
    padding: 15px 0 0 16px;
    font-size: 12.5px;
    line-height: 17.5px;
  }
  .card--back-lower .contact-box { padding-left: 25px; }
  strong { font-weight: 700; }
</style>
</head>
<body>

  <section class="card card--front-dark">
    <div class="block panel-photo--wide panel-photo--dark" role="img" aria-label="Dark grey wavy 3D wall panel installation beside a stairway, with a dining room and lake view on the right"></div>
    <div class="block brand-block brand-block--front">Ripplecraft<br>Facades</div>
  </section>

  <section class="card card--back-upper">
    <p class="tagline">decorative panels for interiors &amp; exteriors</p>
    <div class="block person-box">
      <p class="person-name">Daniel Whitford</p>
      <p>managing director</p>
      <p class="person-mobile">M <strong>0412 308 614</strong></p>
    </div>
    <div class="block panel-photo--strip" role="img" aria-label="Wavy 3D wall panel feature wall with dining area and lake view"></div>
    <div class="block brand-block brand-block--back">Ripplecraft<br>Facades</div>
    <div class="block contact-box">
      <p>P <strong>02 8836 1450</strong>&nbsp; F <strong>02 8836 1459</strong></p>
      <p>14 Carrow Lane, Smithfield NSW 2178</p>
      <p>sales@ripplecraftfacades.com.au</p>
      <p><strong>www.ripplecraftfacades.com.au</strong></p>
    </div>
  </section>

  <section class="card card--front-light">
    <div class="block panel-photo--wide panel-photo--light" role="img" aria-label="White wavy 3D wall panel surface close-up"></div>
    <div class="block brand-block brand-block--front">Ripplecraft<br>Facades</div>
  </section>

  <section class="card card--back-lower">
    <div class="block person-box">
      <p class="person-name">Daniel Whitford</p>
      <p>managing director</p>
      <p class="person-mobile">M <strong>0412 308 614</strong></p>
    </div>
    <div class="block panel-photo--strip" role="img" aria-label="Wavy 3D wall panel feature wall with dining area and lake view"></div>
    <p class="tagline">decorative panels for interiors &amp; exteriors</p>
    <div class="block brand-block brand-block--back">Ripplecraft<br>Facades</div>
    <div class="block contact-box">
      <p>P <strong>02 8836 1450</strong>&nbsp; F <strong>02 8836 1459</strong></p>
      <p>14 Carrow Lane, Smithfield NSW 2178</p>
      <p>sales@ripplecraftfacades.com.au</p>
      <p><strong>www.ripplecraftfacades.com.au</strong></p>
    </div>
  </section>

</body>
</html>
```